Vorlanta PowerPoint Template

I have a company called Vorlanta, LLC and my company logo is already designed. I need a PowerPoint template that I will be using to pitch potential investors and business partners. This should be a very professional-looking template that leverages the company logo colors and really pops. The company is an AI product research and development company.

```html
<!DOCTYPE html>
<html lang="en">
<head>
<meta charset="utf-8">
<title>Vorlanta Presentation Template</title>
<link rel="stylesheet" href="https://fonts.googleapis.com/css2?family=Montserrat:wght@400;500;600&family=Nunito:wght@700;800;900&display=swap">
<style>
  :root {
    --canvas: #666666;
    --paper: #ffffff;
    --brand-red: #b5121b;
    --bright-red: #e0141e;
    --ink: #2b2b2b;
    --muted: #6d6d6d;
    --line: #e2e2e2;
    --heading: "Nunito", sans-serif;
    --body: "Montserrat", sans-serif;
  }
  * { box-sizing: border-box; margin: 0; padding: 0; }
  html, body { width: 997px; height: 1200px; overflow: hidden; background: var(--canvas); }
  body { position: relative; font-family: var(--body); color: var(--ink); }

  .slide {
    position: absolute; width: 427px; height: 240px; background: var(--paper);
    overflow: hidden; box-shadow: 0 1px 3px rgba(0,0,0,.25);
  }
  .col-left { left: 57px; } .col-right { left: 514px; }
  .row-1 { top: 50px; } .row-2 { top: 336px; } .row-3 { top: 623px; } .row-4 { top: 909px; }

  .brand { position: absolute; top: 6px; right: 8px; display: flex; align-items: center; gap: 4px; }
  .brand-dot { width: 18px; height: 18px; border-radius: 50%; background: var(--brand-red); }
  .brand-name { font-family: var(--body); font-weight: 600; font-size: 15px; color: var(--brand-red); letter-spacing: -.3px; }

  .accent { position: absolute; width: 24px; height: 2px; background: var(--brand-red); }
  .title { position: absolute; font-family: var(--heading); font-weight: 800; font-size: 14px; color: var(--ink); white-space: nowrap; }
  .title em { font-style: normal; color: var(--brand-red); }
  .copy { position: absolute; font-size: 6.1px; line-height: 9.4px; color: var(--muted); }

  .footer-note { position: absolute; left: 19px; top: 222px; font-size: 6px; color: var(--muted); }
  .page-no { position: absolute; right: 19px; top: 222px; font-size: 6px; color: var(--muted); }
  .page-no b { color: var(--brand-red); font-weight: 600; font-size: 7px; margin-left: 2px; }

  .media { position: absolute; }

  /* cover */
  .cover-hero { left: 0; top: 0; width: 427px; height: 167px;
    background: radial-gradient(circle at 55% 45%, #c98ad9 0%, #7a3a9c 20%, #35185f 55%, #150b2c 100%); }
  .cover-rule { position: absolute; left: 0; top: 168px; width: 427px; height: 3px; background: var(--bright-red); }
  .cover-rule-thin { position: absolute; left: 0; top: 173px; width: 427px; height: 1px; background: var(--brand-red); }
  .cover-brand { position: absolute; left: 15px; top: 194px; display: flex; align-items: center; gap: 6px; }
  .cover-brand .brand-dot { width: 25px; height: 25px; }
  .cover-brand .brand-name { font-size: 22px; }
  .cover-divider { position: absolute; left: 146px; top: 196px; width: 1.5px; height: 22px; background: var(--brand-red); }
  .cover-title { position: absolute; left: 160px; top: 192px; font-family: var(--heading); font-weight: 800; font-size: 14px; letter-spacing: .6px; color: var(--brand-red); }
  .cover-sub { position: absolute; left: 160px; top: 211px; font-size: 7.3px; color: var(--ink); }

  /* contents list */
  .toc { position: absolute; left: 231px; top: 43px; width: 176px; list-style: none; }
  .toc li { height: 20px; margin-bottom: 6.7px; display: flex; justify-content: space-between; align-items: center;
    padding: 0 11px; font-size: 6.4px; color: var(--muted); background: var(--paper);
    border: 1px solid var(--line); border-radius: 2px; box-shadow: 0 1px 2px rgba(0,0,0,.12); }
  .toc li.is-current { background: var(--bright-red); border-color: var(--bright-red); color: #fff; }

  /* values grid */
  .value { position: absolute; width: 118px; text-align: center; }
  .value-letter { font-size: 9px; color: var(--ink); line-height: 10px; }
  .value-name { font-family: var(--heading); font-weight: 800; font-size: 7.2px; margin-top: 1px; }
  .value-text { font-size: 3.6px; line-height: 5.6px; color: var(--muted); margin: 5px auto 0; width: 104px; }
  .value.is-featured { border: 1px solid var(--line); box-shadow: 0 1px 3px rgba(0,0,0,.2); height: 60px; padding-top: 7px; }
  .value.is-featured .value-letter, .value.is-featured .value-name, .value.is-featured .value-text { color: var(--bright-red); }

  /* goal */
  .goal-hero { left: 0; top: 0; width: 427px; height: 139px; background: linear-gradient(180deg, #e9e9e9 0%, #cfcfcf 100%); }
  .goal-band { position: absolute; left: 57px; top: 114px; width: 312px; height: 82px; background: var(--brand-red); }
  .goal-band .bar { position: absolute; left: 109px; top: 23px; width: 24px; height: 2px; background: #fff; }
  .goal-title { position: absolute; right: 178px; top: 28px; text-align: right; font-family: var(--heading); font-weight: 800;
    font-size: 13.5px; line-height: 17px; color: #fff; }
  .goal-text { position: absolute; left: 154px; top: 25px; width: 142px; font-size: 6px; line-height: 9.4px; color: #fff; }

  /* plans */
  .plan { position: absolute; top: 86px; width: 119px; text-align: center; }
  .plan-photo { width: 119px; height: 79px; }
  .plan-name { font-family: var(--heading); font-weight: 800; font-size: 7.2px; color: var(--brand-red); margin-top: 6px; }
  .plan-text { font-size: 3.6px; line-height: 5.6px; color: var(--muted); margin: 2px auto 0; width: 102px; }

  /* contact */
  .contact { position: absolute; left: 255px; }
  .contact dt { font-size: 8px; font-weight: 500; color: var(--ink); margin-top: 9px; }
  .contact dt:first-child { margin-top: 0; }
  .contact dd { font-size: 7.8px; line-height: 11px; color: var(--ink); margin-top: 4px; }
</style>
</head>
<body>

<!-- Cover -->
<section class="slide col-left row-1">
  <div class="media cover-hero" role="img" aria-label="Cosmic AI artwork: human hand reaching toward a robot hand around a glowing AI chip"></div>
  <div class="cover-rule"></div>
  <div class="cover-rule-thin"></div>
  <div class="cover-brand"><span class="brand-dot"></span><span class="brand-name">Vorlanta</span></div>
  <div class="cover-divider"></div>
  <h1 class="cover-title">PRESENTATION&nbsp; TITLE</h1>
  <p class="cover-sub">Here a Place for Credintial Presentation</p>
</section>

<!-- Presentation list -->
<section class="slide col-right row-1">
  <div class="brand"><span class="brand-dot"></span><span class="brand-name">Vorlanta</span></div>
  <div class="accent" style="left:19px;top:84px"></div>
  <h2 class="title" style="left:19px;top:90px">Presentation <em>List</em></h2>
  <p class="copy" style="left:19px;top:119px;width:185px">Lorem ipsum dolor sit amet, consectetur adipiscing elit, sed do eiusmod tempor incididunt ut labore et dolore magna aliqua. Ut enim ad minim veniam, quis nostrud exercitation ullamco laboris nisi ut aliquip</p>
  <ul class="toc">
    <li><span>01. Section One</span><span>02</span></li>
    <li class="is-current"><span>02. Section Two</span><span>04</span></li>
    <li><span>03. Section Three</span><span>05</span></li>
    <li><span>04. Section Four</span><span>07</span></li>
    <li><span>05. Section Five</span><span>08</span></li>
    <li><span>06. Section Six</span><span>10</span></li>
  </ul>
  <p class="footer-note">Copyright © 2025 Vorlanta. All rights reserved.</p>
  <p class="page-no">Page<b>2</b></p>
</section>

<!-- Welcome -->
<section class="slide col-left row-2">
  <div class="brand"><span class="brand-dot"></span><span class="brand-name">Vorlanta</span></div>
  <div class="media" style="left:19px;top:53px;width:82px;height:134px;border-radius:4px;background:linear-gradient(135deg,#3a3a3a,#0e0e0e)" role="img" aria-label="Black and white photo of a humanoid robot in a thinking pose"></div>
  <div class="media" style="left:112px;top:38px;width:100px;height:163px;border-radius:3px;background:radial-gradient(circle at 50% 50%,#9a0f16,#5e0509);box-shadow:0 2px 4px rgba(0,0,0,.3)" role="img" aria-label="Red circuit board illustration with AI lettering"></div>
  <div class="accent" style="left:236px;top:63px"></div>
  <h2 class="title" style="left:235px;top:69px">Welcome To <em>Vorlanta</em></h2>
  <p class="copy" style="left:236px;top:98px;width:172px">Lorem ipsum dolor sit amet, consectetur adipiscing elit, sed do eiusmod tempor incididunt ut labore et dolore magna aliqua. Ut enim ad minim veniam, quis nostrud exercitation ullamco laboris nisi ut aliquip</p>
  <p class="copy" style="left:236px;top:146px;width:172px">Lorem ipsum dolor sit amet, consectetur adipiscing elit, sed do eiusmod tempor incididunt ut labore et dolore magna aliqua. Ut enim ad minim veniam</p>
  <p class="footer-note">Copyright © 2025 Vorlanta. All rights reserved.</p>
  <p class="page-no">Page<b>3</b></p>
</section>

<!-- Values -->
<section class="slide col-right row-2">
  <div class="brand"><span class="brand-dot"></span><span class="brand-name">Vorlanta</span></div>
  <div class="accent" style="left:155px;top:23px"></div>
  <h2 class="title" style="left:155px;top:29px">Value Of <em>Vorlanta</em></h2>
  <div class="value" style="left:25px;top:74px"><div class="value-letter">D</div><div class="value-name">Development</div><p class="value-text">Focused research turning early ideas into dependable AI products for partners.</p></div>
  <div class="value is-featured" style="left:155px;top:66px"><div class="value-letter">P</div><div class="value-name">Productive</div><p class="value-text">Focused research turning early ideas into dependable AI products for partners.</p></div>
  <div class="value" style="left:284px;top:74px"><div class="value-letter">I</div><div class="value-name">Innovation</div><p class="value-text">Focused research turning early ideas into dependable AI products for partners.</p></div>
  <div class="value" style="left:25px;top:142px"><div class="value-letter">G</div><div class="value-name">Globalism</div><p class="value-text">Focused research turning early ideas into dependable AI products for partners.</p></div>
  <div class="value" style="left:155px;top:142px"><div class="value-letter">Pr</div><div class="value-name">Profit</div><p class="value-text">Focused research turning early ideas into dependable AI products for partners.</p></div>
  <div class="value" style="left:284px;top:142px"><div class="value-letter">T</div><div class="value-name">Technology</div><p class="value-text">Focused research turning early ideas into dependable AI products for partners.</p></div>
  <p class="footer-note">Copyright © 2025 Vorlanta. All rights reserved.</p>
  <p class="page-no">Page<b>4</b></p>
</section>

<!-- Goal -->
<section class="slide col-left row-3">
  <div class="media goal-hero" role="img" aria-label="Wireframe polygon figure holding a glowing AI sphere on a light grey background"></div>
  <div class="brand"><span class="brand-dot"></span><span class="brand-name">Vorlanta</span></div>
  <div class="goal-band">
    <div class="bar"></div>
    <h2 class="goal-title">Our Professional<br>Goal</h2>
    <p class="goal-text">Lorem ipsum dolor sit amet, consectetur adipiscing elit, sed do eiusmod tempor incididunt ut labore et dolore magna aliqua. Ut enim ad minim veniam, quis nostrud</p>
  </div>
  <p class="footer-note">Copyright © 2025 Vorlanta. All rights reserved.</p>
  <p class="page-no">Page<b>5</b></p>
</section>

<!-- Plans -->
<section class="slide col-right row-3">
  <div class="brand"><span class="brand-dot"></span><span class="brand-name">Vorlanta</span></div>
  <div class="accent" style="left:155px;top:23px"></div>
  <h2 class="title" style="left:155px;top:29px">Plans Of <em>Vorlanta</em></h2>
  <p class="copy" style="left:50px;top:53px;width:327px;text-align:center">Lorem ipsum dolor sit amet, consectetur adipiscing elit, sed do eiusmod tempor incididunt ut labore et dolore magna aliqua. Ut enim ad minim veniam, quis nostrud exercitation ullamco</p>
  <div class="plan" style="left:19px"><div class="plan-photo" role="img" aria-label="Team reviewing data on screens in a tech office" style="background:linear-gradient(135deg,#2f5d8a,#13283f)"></div><div class="plan-name">Vorlanta Plan One</div><p class="plan-text">Practical research roadmap with clear milestones, shared results and steady delivery.</p></div>
  <div class="plan" style="left:154px"><div class="plan-photo" role="img" aria-label="Person using a laptop with AI interface overlays" style="background:linear-gradient(135deg,#2d5a86,#0f1d2e)"></div><div class="plan-name">Vorlanta Plan Two</div><p class="plan-text">Practical research roadmap with clear milestones, shared results and steady delivery.</p></div>
  <div class="plan" style="left:289px"><div class="plan-photo" role="img" aria-label="Smartphone showing an AI chat screen with code in the background" style="background:linear-gradient(135deg,#1d6b7a,#0c2230 60%,#6a4a1a)"></div><div class="plan-name">Vorlanta Plan Three</div><p class="plan-text">Practical research roadmap with clear milestones, shared results and steady delivery.</p></div>
  <p class="footer-note">Copyright © 2025 Vorlanta. All rights reserved.</p>
  <p class="page-no">Page<b>6</b></p>
</section>

<!-- Blank -->
<section class="slide col-left row-4">
  <div class="brand"><span class="brand-dot"></span><span class="brand-name">Vorlanta</span></div>
  <div class="accent" style="left:19px;top:23px"></div>
  <h2 class="title" style="left:19px;top:29px">Blank Slide Of <em>Vorlanta</em></h2>
  <p class="footer-note">Copyright © 2025 Vorlanta. All rights reserved.</p>
  <p class="page-no">Page<b>7</b></p>
</section>

<!-- Contact -->
<section class="slide col-right row-4">
  <div class="brand"><span class="brand-dot"></span><span class="brand-name">Vorlanta</span></div>
  <div class="media" style="left:46px;top:52px;width:167px;height:135px;background:linear-gradient(135deg,#2a3a4c,#6b7886 55%,#c49a72)" role="img" aria-label="Hands typing on a laptop with a glowing digital AI head projection"></div>
  <div class="accent" style="left:255px;top:46px"></div>
  <h2 class="title" style="left:255px;top:52px">Contact <em>Us</em></h2>
  <dl class="contact" style="top:85px">
    <dt>Address</dt><dd>147, Ut enim ad minima veniam,<br>exercitationem</dd>
    <dt>Phone</dt><dd>+1 8888-888-888</dd>
    <dt>Email</dt><dd>info@vorlanta.com</dd>
  </dl>
  <p class="footer-note">Copyright © 2025 Vorlanta. All rights reserved.</p>
  <p class="page-no">Page<b>8</b></p>
</section>

</body>
</html>
```